Ridgeline Journeys business card

please see website
www.ridgelinejourneys.comau

info needed on card
Curtis Halvey
Ph
email
Adventure Riding GPS trails

please use my logo and colours off my site

Curtis Halvey
curtis@ridgelinejourneys.com

```html
<!DOCTYPE html>
<html lang="en">
<head>
<meta charset="utf-8">
<title>Ridgeline Journeys – Business Card</title>
<link rel="stylesheet" href="https://fonts.googleapis.com/css2?family=Oswald:wght@700&family=Roboto:wght@400;500&display=swap">
<style>
  :root {
    --stage: #2b2b2b;
    --card-black: #0b0b0b;
    --card-white: #ffffff;
    --brand-yellow: #f5d000;
    --ink-white: #f2f2f2;
    --ink-black: #111111;
    --rule-grey: #8a8a8a;
  }
  html, body {
    margin: 0;
    padding: 0;
    width: 1200px;
    height: 750px;
    overflow: hidden;
    background: var(--stage);
  }
  .stage {
    position: relative;
    width: 1200px;
    height: 750px;
    display: flex;
    align-items: center;
    justify-content: center;
    gap: 60px;
  }
  .card {
    width: 520px;
    height: 300px;
    box-shadow: 0 18px 40px rgba(0,0,0,0.55);
    display: block;
  }
  .brand-name {
    font-family: "Oswald", sans-serif;
    font-weight: 700;
    letter-spacing: 0.5px;
  }
  .tagline {
    font-family: "Roboto", sans-serif;
    font-weight: 400;
    font-size: 13px;
  }
  .person-name {
    font-family: "Roboto", sans-serif;
    font-weight: 500;
    font-size: 19px;
    fill: var(--brand-yellow);
  }
  .contact-line {
    font-family: "Roboto", sans-serif;
    font-weight: 400;
    font-size: 11.5px;
    fill: var(--ink-white);
  }
</style>
</head>
<body>
<main class="stage">

  <!-- Front of card -->
  <svg class="card card-front" viewBox="0 0 520 300" xmlns="http://www.w3.org/2000/svg">
    <rect width="520" height="300" fill="var(--card-black)"/>
    <g class="brand-lockup">
      <circle cx="178" cy="145" r="24" fill="var(--brand-yellow)"/>
      <text class="brand-name" x="216" y="138" font-size="30" fill="var(--ink-white)">RIDGELINE</text>
      <text class="brand-name" x="216" y="172" font-size="30" fill="var(--ink-white)">JOURNEYS</text>
    </g>
    <text class="tagline" x="260" y="232" text-anchor="middle" fill="var(--ink-white)">Adventure Riding GPS trails</text>
  </svg>

  <!-- Back of card -->
  <svg class="card card-back" viewBox="0 0 520 300" xmlns="http://www.w3.org/2000/svg">
    <rect width="520" height="300" fill="var(--card-white)"/>
    <path class="swoosh-accent" d="M0,183 C120,243 250,158 520,36 L520,300 L0,300 Z" fill="var(--brand-yellow)"/>
    <path class="swoosh-white-gap" d="M0,189 C120,249 250,164 520,44 L520,300 L0,300 Z" fill="var(--card-white)"/>
    <path class="swoosh-band" d="M0,195 C120,255 250,170 520,50 L520,300 L0,300 Z" fill="var(--card-black)"/>

    <g class="brand-lockup">
      <circle cx="150" cy="92" r="24" fill="var(--brand-yellow)"/>
      <text class="brand-name" x="188" y="85" font-size="28" fill="var(--ink-black)">RIDGELINE</text>
      <text class="brand-name" x="188" y="117" font-size="28" fill="var(--ink-black)">JOURNEYS</text>
    </g>

    <text class="person-name" x="268" y="252" text-anchor="end">Curtis Halvey</text>
    <line class="divider" x1="282" y1="190" x2="282" y2="260" stroke="var(--rule-grey)" stroke-width="1"/>

    <g class="contact-list">
      <g class="icon-phone" fill="var(--brand-yellow)">
        <path d="M295,194 h10 a2,2 0 0 1 2,2 v2 h-3 v-1 h-8 v1 h-3 v-2 a2,2 0 0 1 2,-2 z"/>
        <rect x="296" y="199" width="8" height="6" rx="1"/>
      </g>
      <text class="contact-line" x="314" y="204">555 0148 2290</text>

      <g class="icon-mail">
        <rect x="294" y="213" width="13" height="9" fill="var(--brand-yellow)"/>
        <path d="M294,213 L300.5,218.5 L307,213" fill="none" stroke="var(--card-black)" stroke-width="1.2"/>
      </g>
      <text class="contact-line" x="314" y="222">curtis@ridgelinejourneys.com</text>

      <g class="icon-web">
        <circle cx="300.5" cy="235.5" r="6" fill="var(--brand-yellow)"/>
        <circle cx="300.5" cy="235.5" r="2" fill="var(--card-black)"/>
      </g>
      <text class="contact-line" x="314" y="240">www.ridgelinejourneys.com.au</text>
    </g>

    <text class="tagline" x="300" y="282" fill="var(--ink-white)">Adventure Riding GPS trails</text>
  </svg>

</main>
</body>
</html>
```